Business Card Design for Training Business

Clear Path Coaching is a new business that delivers training and other services with a focus on topics related to mental health and wellbeing, for example, Wellmind Response Course, Resilience etc. We have a strong focus on evidence-based psychology and neuroscience. I have a logo which I will upload with the brief, so please consider colours that work well with the logo.
Target Market(s)
Adults, workplaces (particularly government and not-for-profits)
Industry/Entity Type
Business
Contact Information for Business Card
Head Strong TrainingSamantha SellwoodDirector0438 770 850sam@headstrongtraining.com.auwww.headstrongtraining.com.au

```html
<!DOCTYPE html>
<html lang="en">
<head>
<meta charset="utf-8">
<title>Clear Path Coaching – Business Card</title>
<link rel="stylesheet" href="https://fonts.googleapis.com/css2?family=Open+Sans:wght@300;400;600&display=swap">
<style>
  :root {
    --page: #e9e6e1;
    --card: #0b0b0c;
    --card-sheen: #1c1c1e;
    --teal: #2fb8c4;
    --teal-light: #5fd3dc;
    --text-light: #d9d9d9;
    --text-muted: #a7a7a7;
    --white: #ffffff;
  }
  * { margin: 0; padding: 0; box-sizing: border-box; }
  html, body {
    width: 1200px; height: 1023px; overflow: hidden;
    background: var(--page);
    font-family: "Open Sans", Arial, sans-serif;
  }
  .sheet {
    width: 1200px; height: 1023px;
    display: flex; flex-direction: column; align-items: center; justify-content: center;
    gap: 44px;
  }
  .card {
    position: relative;
    width: 800px; height: 457px;
    background: linear-gradient(135deg, var(--card-sheen) 0%, var(--card) 55%);
    border-radius: 6px;
    overflow: hidden;
    box-shadow: 0 10px 30px rgba(0,0,0,0.25);
  }
  .edge-band {
    position: absolute; top: 36px; bottom: 36px; width: 16px;
    background: linear-gradient(90deg, var(--teal-light), var(--teal));
    border-radius: 8px;
  }
  .edge-band--left { left: -6px; }
  .edge-band--right { right: -6px; }

  /* Brand block */
  .brand {
    display: flex; flex-direction: column; align-items: center; gap: 22px;
  }
  .brand__dot {
    width: 92px; height: 92px; border-radius: 50%;
    border: 2px solid var(--teal);
  }
  .brand__name {
    color: var(--white); font-weight: 300; font-size: 30px;
    letter-spacing: 3px; text-transform: uppercase; text-align: center; line-height: 1.2;
  }

  /* Front */
  .card--front .contact {
    position: absolute; left: 70px; bottom: 70px;
  }
  .contact__name { color: var(--text-light); font-weight: 300; font-size: 30px; }
  .contact__role { color: var(--teal); font-size: 19px; margin-top: 4px; }
  .contact__company { color: var(--white); font-weight: 600; font-size: 20px; margin-top: 2px; }
  .contact__list { list-style: none; margin-top: 22px; }
  .contact__item {
    display: flex; align-items: center; gap: 14px;
    color: var(--text-light); font-size: 17px; line-height: 30px;
  }
  .contact__icon { width: 18px; height: 18px; flex: none; }
  .divider {
    position: absolute; left: 460px; top: 70px; bottom: 70px; width: 1px;
    background: var(--teal); opacity: 0.8;
  }
  .card--front .brand {
    position: absolute; left: 460px; right: 0; top: 50%; transform: translateY(-50%);
  }

  /* Back */
  .card--back { display: flex; align-items: center; justify-content: center; }
</style>
</head>
<body>
<main class="sheet">
  <section class="card card--front" aria-label="Card front">
    <span class="edge-band edge-band--left"></span>
    <span class="edge-band edge-band--right"></span>
    <div class="contact">
      <p class="contact__name">Rebecca Tanfield</p>
      <p class="contact__role">Manager</p>
      <p class="contact__company">Clear Path Coaching</p>
      <ul class="contact__list">
        <li class="contact__item">
          <svg class="contact__icon" viewBox="0 0 24 24" aria-hidden="true"><path fill="#d9d9d9" d="M6.6 10.8a15.1 15.1 0 0 0 6.6 6.6l2.2-2.2c.3-.3.7-.4 1-.2 1.1.4 2.3.6 3.6.6.6 0 1 .4 1 1V20c0 .6-.4 1-1 1A17 17 0 0 1 3 4c0-.6.4-1 1-1h3.5c.6 0 1 .4 1 1 0 1.3.2 2.5.6 3.6.1.3 0 .7-.2 1z"/></svg>
          0491 362 517
        </li>
        <li class="contact__item">
          <svg class="contact__icon" viewBox="0 0 24 24" aria-hidden="true"><rect x="2" y="5" width="20" height="14" rx="2" fill="#d9d9d9"/><path d="M3 6l9 7 9-7" stroke="#0b0b0c" stroke-width="1.8" fill="none"/></svg>
          bec@clearpathcoaching.example.au
        </li>
        <li class="contact__item">
          <svg class="contact__icon" viewBox="0 0 24 24" aria-hidden="true"><g fill="none" stroke="#d9d9d9" stroke-width="1.8"><circle cx="12" cy="12" r="9.5"/><ellipse cx="12" cy="12" rx="4" ry="9.5"/><path d="M2.5 12h19"/></g></svg>
          www.clearpathcoaching.example.au
        </li>
      </ul>
    </div>
    <span class="divider"></span>
    <div class="brand">
      <span class="brand__dot"></span>
      <p class="brand__name">Clear Path Coaching</p>
    </div>
  </section>

  <section class="card card--back" aria-label="Card back">
    <span class="edge-band edge-band--left"></span>
    <span class="edge-band edge-band--right"></span>
    <div class="brand">
      <span class="brand__dot"></span>
      <p class="brand__name">Clear Path Coaching</p>
    </div>
  </section>
</main>
</body>
</html>
```